Business card for Luxury Portable Restroom Trailer company

We are a Luxury Portable Restroom Trailer Company Called FALCRIDGE HIRES. Based in Orange County California. We provide portable restroom trailers for events, such as, Weddings, Concerts, Charity events, Sporting events, Tournaments, Corporate events, ect. We rent and Sell the Luxury restrooms. Our colors are white, grey, and Orange. As you will see in the logo we uploaded.
There are 2 people in the company so the names and titles will change for the 3 people but card will remain the same. Here is the information for each Person: Dwight Penner CFO 555 318-0476
next Person: Leon Marchetti VP 555 318-0476
Next Person: Owen Marchetti CEO 555 318-0476
Information to include on the card: Luxury Restroom Trailers Rental and Sales. Weddings, Concerts, Charity, Sporting and Corp. Events.

```html
<!DOCTYPE html>
<html lang="en">
<head>
<meta charset="utf-8">
<title>Falcridge Hires – Business Card</title>
<link href="https://fonts.googleapis.com/css2?family=Montserrat:wght@400;500;600;800&display=swap" rel="stylesheet">
<style>
  :root {
    --backdrop: #1a1a1a;
    --card: #232323;
    --orange: #f26a21;
    --white: #f4f4f4;
    --grey: #3a3a3a;
  }
  * { box-sizing: border-box; margin: 0; padding: 0; }
  html, body { width: 1200px; height: 801px; overflow: hidden; }
  body {
    background: var(--backdrop);
    font-family: "Montserrat", sans-serif;
    display: flex;
    align-items: center;
    justify-content: center;
    gap: 40px;
  }
  .card {
    width: 530px;
    height: 303px;
    background: var(--card);
    border-bottom: 3px solid var(--orange);
    position: relative;
    overflow: hidden;
  }
  /* Front */
  .card-front { display: flex; align-items: center; }
  .brand-block {
    width: 50%;
    display: flex;
    justify-content: center;
    align-items: center;
  }
  .brand-name {
    color: var(--orange);
    font-weight: 800;
    font-size: 24px;
    letter-spacing: 1px;
    display: flex;
    align-items: center;
    gap: 8px;
  }
  .brand-mark {
    width: 14px; height: 14px;
    background: var(--orange);
  }
  .divider {
    width: 1px;
    height: 120px;
    background: var(--orange);
    opacity: .8;
  }
  .contact-block { padding-left: 28px; }
  .person-name {
    color: var(--orange);
    font-weight: 800;
    font-size: 20px;
    letter-spacing: 1px;
    text-transform: uppercase;
  }
  .person-title {
    color: var(--white);
    font-size: 13px;
    margin: 2px 0 16px;
  }
  .contact-list { list-style: none; }
  .contact-list li {
    color: var(--white);
    font-size: 12px;
    display: flex;
    align-items: center;
    gap: 8px;
    margin-bottom: 6px;
  }
  .contact-list svg { width: 11px; height: 11px; fill: var(--orange); flex: none; }
  /* Back */
  .card-back {
    display: flex;
    flex-direction: column;
    align-items: center;
    justify-content: center;
  }
  .brand-emboss {
    color: var(--grey);
    font-weight: 800;
    font-size: 46px;
    letter-spacing: 2px;
    margin-bottom: 34px;
  }
  .tagline {
    color: var(--orange);
    font-weight: 600;
    font-size: 14px;
    letter-spacing: .3px;
  }
  .services {
    color: var(--white);
    font-size: 14px;
    margin-top: 6px;
    letter-spacing: .3px;
  }
</style>
</head>
<body>
  <section class="card card-front">
    <div class="brand-block">
      <div class="brand-name"><span class="brand-mark"></span>FALCRIDGE HIRES</div>
    </div>
    <div class="divider"></div>
    <div class="contact-block">
      <h1 class="person-name">Owen Marchetti</h1>
      <p class="person-title">CEO</p>
      <ul class="contact-list">
        <li><svg viewBox="0 0 24 24"><path d="M6.6 10.8a15 15 0 0 0 6.6 6.6l2.2-2.2a1 1 0 0 1 1-.25 11.4 11.4 0 0 0 3.6.57 1 1 0 0 1 1 1V20a1 1 0 0 1-1 1A17 17 0 0 1 3 4a1 1 0 0 1 1-1h3.5a1 1 0 0 1 1 1 11.4 11.4 0 0 0 .57 3.6 1 1 0 0 1-.25 1z"/></svg>555 318-0476</li>
        <li><svg viewBox="0 0 24 24"><path d="M2 5h20v14H2z M2 5l10 8 10-8" /></svg>owen@falcridgehires.com</li>
        <li><svg viewBox="0 0 24 24"><circle cx="12" cy="12" r="10"/></svg>www.falcridgehires.com</li>
      </ul>
    </div>
  </section>

  <section class="card card-back">
    <div class="brand-emboss">FALCRIDGE HIRES</div>
    <p class="tagline">Luxury Restroom Trailers Rental and Sales</p>
    <p class="services">Weddings | Concerts | Charity | Sporting | Corp</p>
  </section>
</body>
</html>
```